Velmora Freightway Solutions Business cards

Would like a very unique design catchy but professional for business cards. Please use log provided.Marlon WellsCeo and Founder TransCon Logistix Solutions1-888-913-3225mwells@tlsolutionsus.comwww.tlsolutionsus.com

```html
<!DOCTYPE html>
<html lang="en">
<head>
<meta charset="utf-8">
<title>Velmora Freightway Solutions – Business Cards</title>
<link rel="stylesheet" href="https://fonts.googleapis.com/css2?family=Cinzel:wght@700&family=Lato:wght@400;700&display=swap">
<style>
  :root {
    --backdrop: #1d1d1d;
    --card: #0b0b0b;
    --card-edge: #151515;
    --brand-blue: #1f78c8;
    --brand-red: #e3262e;
    --silver: #b9b9b9;
    --silver-dim: #6d6d6d;
    --ink-light: #f2f2f2;
  }
  * { box-sizing: border-box; margin: 0; padding: 0; }
  html, body { width: 1200px; height: 1200px; overflow: hidden; }
  body {
    background: var(--backdrop);
    font-family: "Lato", sans-serif;
    position: relative;
  }
  .card {
    position: absolute;
    left: 250px;
    width: 700px;
    height: 400px;
    border-radius: 22px;
    background: linear-gradient(160deg, var(--card-edge), var(--card) 60%);
    box-shadow: 0 18px 40px rgba(0,0,0,.55);
  }
  .card--back { top: 140px; }
  .card--front { top: 660px; }

  /* Back side */
  .back-brand {
    position: absolute;
    top: 140px; left: 0; right: 0;
    text-align: center;
  }
  .back-brand .brand-name {
    font-family: "Cinzel", serif;
    font-weight: 700;
    font-size: 34px;
    letter-spacing: 3px;
    color: var(--silver);
    display: inline-flex;
    align-items: center;
    gap: 14px;
  }
  .back-brand .brand-mark {
    width: 18px; height: 18px;
    background: var(--silver);
  }
  .back-brand .brand-rule {
    width: 460px; height: 2px;
    margin: 16px auto 0;
    background: linear-gradient(90deg, transparent, var(--silver-dim), var(--silver), transparent);
  }
  .back-url {
    position: absolute;
    bottom: 80px; left: 0; right: 0;
    text-align: center;
    font-family: "Cinzel", serif;
    font-weight: 700;
    font-size: 17px;
    letter-spacing: 3px;
    color: var(--silver-dim);
  }

  /* Front side */
  .front-brand {
    position: absolute;
    left: 36px; top: 150px;
    width: 330px;
    text-align: center;
  }
  .front-brand .brand-name {
    font-family: "Cinzel", serif;
    font-weight: 700;
    font-size: 26px;
    line-height: 1.25;
    letter-spacing: 2px;
    color: var(--brand-blue);
  }
  .front-brand .brand-rule {
    height: 3px;
    margin-top: 12px;
    background: linear-gradient(90deg, transparent, var(--brand-red) 20%, var(--brand-red) 80%, transparent);
  }
  .divider {
    position: absolute;
    left: 390px; top: 110px;
    width: 1px; height: 170px;
    background: linear-gradient(transparent, #cfcfcf, transparent);
  }
  .contact {
    position: absolute;
    left: 420px; top: 138px;
  }
  .contact .person-name {
    font-family: "Cinzel", serif;
    font-weight: 700;
    font-size: 26px;
    letter-spacing: 1px;
    color: var(--brand-blue);
  }
  .contact .person-role {
    font-family: "Cinzel", serif;
    font-weight: 700;
    font-size: 16px;
    color: var(--brand-red);
    margin-top: 2px;
  }
  .contact-list { list-style: none; margin-top: 16px; }
  .contact-list li {
    display: flex;
    align-items: center;
    gap: 14px;
    font-size: 19px;
    color: var(--ink-light);
    line-height: 30px;
  }
  .contact-list svg { width: 18px; height: 18px; flex: none; }
</style>
</head>
<body>

  <section class="card card--back" aria-label="Business card, back side">
    <div class="back-brand">
      <div class="brand-name"><span class="brand-mark"></span>Velmora Freightway Solutions</div>
      <div class="brand-rule"></div>
    </div>
    <div class="back-url">WWW.VFWAYROUTES.COM</div>
  </section>

  <section class="card card--front" aria-label="Business card, front side">
    <div class="front-brand">
      <div class="brand-name">Velmora Freightway Solutions</div>
      <div class="brand-rule"></div>
    </div>

    <div class="divider"></div>

    <div class="contact">
      <h1 class="person-name">DORIAN PIKE</h1>
      <p class="person-role">CEO AND FOUNDER</p>
      <ul class="contact-list">
        <li>
          <svg viewBox="0 0 24 24" aria-hidden="true"><path fill="#e3262e" d="M6.6 10.8a15.1 15.1 0 0 0 6.6 6.6l2.2-2.2a1 1 0 0 1 1-.25 11.4 11.4 0 0 0 3.6.57 1 1 0 0 1 1 1V20a1 1 0 0 1-1 1A17 17 0 0 1 3 4a1 1 0 0 1 1-1h3.5a1 1 0 0 1 1 1c0 1.25.2 2.45.57 3.57a1 1 0 0 1-.25 1z"/></svg>
          1-888-470-6158
        </li>
        <li>
          <svg viewBox="0 0 24 24" aria-hidden="true"><g fill="none" stroke="#e3262e" stroke-width="2"><circle cx="12" cy="12" r="9"/><ellipse cx="12" cy="12" rx="4" ry="9"/><path d="M3 12h18M5 7h14M5 17h14"/></g></svg>
          dpike@vfwayroutes.com
        </li>
        <li>
          <svg viewBox="0 0 24 24" aria-hidden="true"><rect x="2" y="5" width="20" height="14" fill="#e3262e"/><path d="M2 5l10 8 10-8" fill="none" stroke="#0b0b0b" stroke-width="1.6"/></svg>
          www.vfwayroutes.com
        </li>
      </ul>
    </div>
  </section>

</body>
</html>
```